Business Card

Just need business logo with phone number on it. 0487 312 654
And the following on the bottom of the card.

"Your local plumbing experts".
and emblems for zelpa card, cheque and cash

```html
<!DOCTYPE html>
<html lang="en">
<head>
<meta charset="utf-8">
<title>Northgate Plumbing &amp; Drainage – Business Card</title>
<link rel="stylesheet" href="https://fonts.googleapis.com/css2?family=Michroma&family=Roboto:wght@400;700&display=swap">
<style>
  :root {
    --backdrop: #2b2b2b;
    --card: #f1f1f1;
    --brand-red: #d62b2b;
    --brand-blue: #1a73c9;
    --cheque: #f3ee96;
    --cheque-line: #8a8a5a;
    --cash: #6fa786;
    --badge-border: #9aa7c4;
  }
  html, body {
    margin: 0;
    width: 1200px;
    height: 902px;
    overflow: hidden;
    background: var(--backdrop);
  }
  .card {
    position: absolute;
    left: 100px;
    top: 165px;
    width: 1000px;
    height: 572px;
    background: var(--card);
    border-radius: 36px;
    font-family: "Roboto", sans-serif;
  }
  .brand {
    position: absolute;
    left: 110px;
    top: 140px;
    display: inline-block;
    color: var(--brand-red);
    font-weight: 700;
    text-transform: uppercase;
    line-height: 1;
    white-space: nowrap;
  }
  .brand-name { display: block; font-size: 56px; letter-spacing: 2px; }
  .brand-trade { display: block; font-size: 23px; letter-spacing: 3px; margin-top: 8px; }
  .brand-suffix { display: block; font-size: 12px; letter-spacing: 2px; margin-top: 6px; text-align: right; }
  .contact {
    position: absolute;
    left: 520px;
    top: 275px;
    white-space: nowrap;
  }
  .phone {
    display: flex;
    align-items: center;
    gap: 14px;
    color: var(--brand-blue);
    font-family: "Michroma", sans-serif;
    font-size: 30px;
    letter-spacing: 1px;
    font-weight: 700;
  }
  .tagline {
    margin-top: 10px;
    color: var(--brand-red);
    font-size: 31px;
  }
  .payment {
    position: absolute;
    left: 470px;
    top: 470px;
    display: flex;
    align-items: center;
    gap: 16px;
    color: var(--brand-blue);
    font-size: 20px;
    white-space: nowrap;
  }
  .pay-zelpa {
    border: 1.5px solid var(--badge-border);
    border-radius: 4px;
    padding: 6px 10px;
    font-weight: 700;
    font-size: 18px;
    color: var(--brand-blue);
    background: #fff;
  }
  .pay-cheque {
    width: 70px;
    height: 34px;
    background: var(--cheque);
    position: relative;
    font-size: 7px;
    color: var(--cheque-line);
  }
  .pay-cheque span { position: absolute; left: 22px; top: 4px; text-transform: uppercase; }
  .pay-cheque i { position: absolute; height: 2px; background: var(--cheque-line); }
  .pay-cash {
    width: 62px;
    height: 32px;
    background: var(--cash);
    color: #eef5ee;
    font-size: 14px;
    font-weight: 700;
    display: flex;
    align-items: center;
    justify-content: center;
  }
</style>
</head>
<body>
  <div class="card">
    <div class="brand">
      <span class="brand-name">Northgate</span>
      <span class="brand-trade">Plumbing &amp; Drainage</span>
      <span class="brand-suffix">Pty Ltd</span>
    </div>

    <div class="contact">
      <div class="phone">
        <svg width="30" height="30" viewBox="0 0 30 30" aria-hidden="true">
          <circle cx="15" cy="15" r="13" fill="none" stroke="var(--brand-blue)" stroke-width="2.5"/>
          <path d="M11 8.5c-1.5 1-2 2.5-1 5s3 5 5.5 6.5 4 1 5-.5l-2.5-2.5-2 1c-1.5-.8-3-2.5-3.7-4l1-2z" fill="var(--brand-blue)"/>
        </svg>
        <span>0487 312 654</span>
      </div>
      <div class="tagline">Your local plumbing experts</div>
    </div>

    <div class="payment">
      <span class="payment-label">Payment made from:</span>
      <span class="pay-zelpa">zelpa</span>
      <span class="pay-cheque"><span>Cheque</span><i style="left:6px;top:16px;width:40px"></i><i style="left:6px;top:24px;width:56px"></i></span>
      <span class="pay-cash">CASH</span>
    </div>
  </div>
</body>
</html>
```